Tall fern bicycle rental

would like to have a bicycle rental website that has the ability to have a calender and be able to sign a liability waiver and pay all on line, We rent fat tire vorn bicycles

```html
<!DOCTYPE html>
<html lang="en">
<head>
<meta charset="utf-8">
<title>Tall Fern Bicycle Rental</title>
<link href="https://fonts.googleapis.com/css2?family=Arimo:wght@400;700&family=Montserrat:wght@700;800&display=swap" rel="stylesheet">
<style>
:root{
  --blue:#1565b0;
  --blue-bright:#2591d9;
  --blue-deep:#1a5fa8;
  --ink:#1b1b1b;
  --text:#555;
  --grey-band:#e4e4e4;
  --footer:#1d1d1f;
  --white:#fff;
}
*{margin:0;padding:0;box-sizing:border-box}
html,body{width:1200px;height:3701px;overflow:hidden;background:var(--white)}
body{position:relative;font-family:"Arimo",Arial,sans-serif;color:var(--text)}
.abs{position:absolute}
/* header */
.brand{left:89px;top:10px;width:150px;text-align:center;color:var(--blue)}
.brand-mark{width:66px;height:66px;border-radius:50%;background:var(--blue);margin:0 auto 4px}
.brand-name{font-family:"Arimo",sans-serif;font-weight:700;font-size:19px;letter-spacing:1px;line-height:1}
.brand-tag{font-size:7px;letter-spacing:.5px;margin-top:3px}
.quote-btn{left:614px;top:34px;width:172px;height:46px;background:var(--blue-bright);color:#fff;font-size:18px;display:flex;align-items:center;justify-content:center}
.social-top{top:34px;left:847px;display:flex;gap:6px}
.social-top span{width:47px;height:46px;border:1px solid #ccc;display:block}
.nav{left:0;top:115px;width:1200px;height:47px;background:var(--blue)}
.nav a{position:absolute;top:15px;color:#fff;font-size:16px;text-decoration:none}
/* hero */
.hero{left:0;top:162px;width:1200px;height:625px;background:radial-gradient(ellipse at 60% 55%,#3d4e63 0%,#283343 40%,#1e2630 70%),#252d38}
.hero-snow{left:0;top:560px;width:1200px;height:120px;background:linear-gradient(#8b97a6,#c9d1dc)}
.hero-title{left:0;width:1200px;text-align:center;color:#fff;font-size:57px;line-height:1}
.field{top:493px;height:50px;background:#fff;font-size:13px;color:#666;padding-left:18px;display:flex;align-items:center}
.search-btn{left:865px;top:493px;width:183px;height:50px;background:var(--blue);color:#fff;font-size:18px;display:flex;align-items:center;justify-content:center}
/* sections */
.photo-circle{border-radius:50%}
.h2{font-family:"Montserrat",sans-serif;font-weight:800;color:var(--ink);font-size:43px;letter-spacing:.5px}
.para{font-size:15.5px;line-height:30.2px;text-align:justify;color:#666}
.btn{background:var(--blue-bright);color:#fff;font-size:16px;display:flex;align-items:center;justify-content:center}
.how-title{left:0;top:1536px;width:1200px;text-align:center;color:#fff}
.how-lead{left:100px;top:1610px;width:1000px;text-align:center;color:#fff;font-size:18px;line-height:29px}
.step{border-radius:50%;text-align:center;display:flex;flex-direction:column;align-items:center}
.step-blue{background:var(--blue-bright);color:#fff;border:3px solid #fff}
.step-white{background:#fff;color:var(--ink);box-shadow:0 6px 10px rgba(0,0,0,.25)}
.step h3{font-weight:400;font-size:27px;line-height:30px}
.step p{font-size:15px;line-height:25px}
.news-title{left:0;top:2956px;width:1200px;text-align:center;font-family:"Montserrat",sans-serif;font-weight:700;font-size:29px;color:var(--ink)}
.news-lead{left:0;top:3010px;width:1200px;text-align:center;font-size:18px;color:var(--ink)}
.email-pill{left:213px;top:3070px;width:773px;height:70px;border-radius:35px;background:#fff}
.email-label{left:260px;top:3093px;font-size:18px;color:var(--ink)}
.signup{left:793px;top:3077px;width:184px;height:56px;border-radius:28px;background:var(--blue-bright);color:#fff;font-size:19px;display:flex;align-items:center;justify-content:center}
.foot-h{color:#fff;font-size:27px}
.foot-p{color:#ddd;font-size:13px;line-height:23px}
.foot-link{color:#ddd;font-size:14px;line-height:25.5px}
.copyright{left:0;top:3600px;width:1200px;text-align:center;color:#fff;font-size:13px}
.social-foot{left:480px;top:3630px;display:flex;gap:7px}
.social-foot span{width:43px;height:42px;border:1px solid var(--blue);display:block}
</style>
</head>
<body>

<!-- header -->
<div class="abs brand">
  <div class="brand-mark"></div>
  <div class="brand-name">TALL FERN</div>
  <div class="brand-tag">BICYCLE RENTAL · FAT TIRE RIDES</div>
</div>
<div class="abs quote-btn">Get a Free Quote</div>
<div class="abs social-top"><span></span><span></span><span></span><span></span><span></span></div>

<nav class="abs nav">
  <a style="left:221px">HOME</a>
  <a style="left:322px">DESTINATION TIPS</a>
  <a style="left:513px">QUESTIONS</a>
  <a style="left:655px">BLOG</a>
  <a style="left:753px">GALLERY</a>
  <a style="left:877px">CONTACT US</a>
</nav>

<!-- hero -->
<div class="abs hero" role="img" aria-label="Fat tire bicycle parked in a snowy pine forest"></div>
<div class="abs hero-snow" style="top:680px" role="img" aria-label="Snow covered ground"></div>
<div class="abs hero-title" style="top:347px">Welcome</div>
<div class="abs hero-title" style="top:408px">Tall Fern Bicycle Rental</div>
<div class="abs field" style="left:151px;width:240px">Where Do You Want To Go ?</div>
<div class="abs field" style="left:402px;width:220px;justify-content:space-between;padding-right:16px">All Type bike<span>⌄</span></div>
<div class="abs field" style="left:634px;width:221px;justify-content:space-between;padding-right:12px">Check Availability
  <svg width="13" height="13" viewBox="0 0 13 13"><rect x="1" y="2" width="11" height="10" fill="none" stroke="#777"/><line x1="1" y1="5" x2="12" y2="5" stroke="#777"/></svg></div>
<div class="abs search-btn">Search</div>
<svg class="abs" style="left:0;top:730px" width="1200" height="70" viewBox="0 0 1200 70">
  <path d="M0 10 C250 45 440 53 560 53 C578 53 578 24 600 24 C622 24 622 53 640 53 C760 53 950 45 1200 10 L1200 70 L0 70 Z" fill="#fff"/>
  <rect x="588" y="30" width="24" height="36" rx="12" fill="none" stroke="#222" stroke-width="2"/>
  <line x1="600" y1="38" x2="600" y2="46" stroke="#222" stroke-width="2"/>
</svg>

<!-- about -->
<div class="abs photo-circle" style="left:122px;top:920px;width:402px;height:402px;background:linear-gradient(160deg,#5a6e5d,#c6d3dc 70%,#eef1f4)" role="img" aria-label="Rider on a fat tire bike in the snowy woods"></div>
<div class="abs h2" style="left:593px;top:940px">ABOUT US</div>
<p class="abs para" style="left:593px;top:1007px;width:485px">Lorem ipsum dolor sit amet, consectetur adipiscing elit, sed do eiusmod tempor incididunt ut labore et dolore magna aliqua. Ut enim ad minim veniam, quis nostrud exercitation ullamco laboris nisi ut aliquip ex ea commodo consequat. Duis aute irure dolor in reprehenderit in voluptate velit esse cillum dolore eu fugiat nulla pariatur. Excepteur sint occaecat cupidatat non proident, sunt in culpa qui officia deserunt mollit anim id est laborum.</p>
<div class="abs btn" style="left:593px;top:1244px;width:157px;height:48px">Read More</div>

<!-- how it works -->
<svg class="abs" style="left:0;top:1437px" width="1200" height="420" viewBox="0 0 1200 420" role="img" aria-label="Blue tinted winter riding scene">
  <defs><linearGradient id="howBand" x1="0" y1="0" x2="0" y2="1"><stop offset="0" stop-color="#1e66b0"/><stop offset="1" stop-color="#1c70c0"/></linearGradient></defs>
  <path d="M0 44 C300 -8 900 -8 1200 44 L1200 390 C900 400 700 410 600 410 C500 410 300 400 0 380 Z" fill="url(#howBand)"/>
</svg>
<div class="abs h2 how-title">HOW DOES IT WORK</div>
<p class="abs how-lead">Lorem ipsum dolor sit amet, consectetur adipiscing elit, sed do eiusmod tempor incididunt ut labore et dolore magna aliqua. Ut enim ad minim veniam, quis nostrud exercitation ullamco laboris nisi ut aliquip ex ea commodo consequat.</p>

<div class="abs step step-blue" style="left:89px;top:1727px;width:340px;height:340px;padding:50px 22px 0">
  <svg width="64" height="64" viewBox="0 0 64 64" fill="none" stroke="#fff" stroke-width="2"><path d="M4 24 L20 18 L32 24 L44 18 L60 24 L60 60 L44 54 L32 60 L20 54 L4 60 Z"/><path d="M32 36 C24 26 24 20 32 6 C40 20 40 26 32 36 Z" fill="var(--blue-bright)"/><circle cx="32" cy="16" r="3"/></svg>
  <h3 style="margin-top:16px">Find the perfect<br>bike(s) for you</h3>
  <p style="margin-top:16px">Lorem ipsum dolor sit amet, consectetur adipiscing elit, sed do eiusmod tempor incididunt</p>
</div>
<div class="abs step step-blue" style="left:762px;top:1727px;width:340px;height:340px;padding:50px 40px 0">
  <svg width="72" height="56" viewBox="0 0 72 56" fill="none" stroke="#fff" stroke-width="2"><circle cx="14" cy="40" r="12"/><circle cx="58" cy="40" r="12"/><path d="M14 40 L26 20 L48 20 L58 40 M26 20 L36 40 L48 20 M44 8 L50 8 L54 20"/></svg>
  <h3 style="margin-top:14px">The bike will be<br>waiting for you!</h3>
  <p style="margin-top:10px">Lorem ipsum dolor sit amet, consectetur adipiscing elit, sed do eiusmod tempor incididunt</p>
</div>
<div class="abs step step-white" style="left:409px;top:1706px;width:382px;height:382px;padding:96px 30px 0">
  <svg width="92" height="60" viewBox="0 0 92 60" fill="none" stroke="var(--blue)" stroke-width="2.5"><rect x="4" y="4" width="30" height="30" rx="4"/><path d="M20 30 L34 44 L88 44 M40 24 L88 24 M46 34 L84 34 M50 54 L80 54"/></svg>
  <h3 style="margin-top:14px;font-size:31px">Book directly online</h3>
  <p style="margin-top:14px;font-size:16px;line-height:28px">Lorem ipsum dolor sit amet,<br>consectetur adipiscing elit, sed do</p>
</div>

<!-- book your ride -->
<div class="abs h2" style="left:91px;top:2268px">BOOK YOUR RIDE</div>
<p class="abs para" style="left:89px;top:2343px;width:477px">Lorem ipsum dolor sit amet, consectetur adipiscing elit, sed do eiusmod tempor incididunt ut labore et dolore magna aliqua. Ut enim ad minim veniam, quis nostrud exercitation ullamco laboris nisi ut aliquip ex ea commodo consequat. Duis aute irure dolor in reprehenderit in voluptate velit esse cillum dolore eu fugiat nulla pariatur. Excepteur sint occaecat cupidatat non proident, sunt in culpa qui officia deserunt mollit anim id est laborum.</p>
<div class="abs btn" style="left:93px;top:2595px;width:157px;height:48px">Calendar</div>
<div class="abs photo-circle" style="left:647px;top:2210px;width:500px;height:500px;background:linear-gradient(170deg,#9aa3ab,#c8cfd6 45%,#e9edf1)" role="img" aria-label="Two riders on fat tire bikes along a snowy trail"></div>

<!-- newsletter -->
<svg class="abs" style="left:0;top:2824px" width="1200" height="480" viewBox="0 0 1200 480">
  <path d="M0 50 C300 -12 900 -12 1200 50 L1200 480 L0 480 Z" fill="var(--grey-band)"/>
</svg>
<div class="abs news-title">DON'T MISS OUT ON DISCOUNTS AND DEALS</div>
<div class="abs news-lead">Lorem ipsum dolor sit amet, consectetur adipiscing elit, sed do eiusmod tempor incididunt</div>
<div class="abs email-pill"></div>
<div class="abs email-label">Email</div>
<div class="abs signup">Sign Up</div>

<!-- footer -->
<svg class="abs" style="left:0;top:3230px" width="1200" height="471" viewBox="0 0 1200 471">
  <path d="M0 52 C250 40 450 30 550 30 C575 30 578 64 600 64 C622 64 625 30 650 30 C750 30 950 40 1200 52 L1200 471 L0 471 Z" fill="var(--footer)"/>
  <rect x="590" y="10" width="20" height="32" rx="10" fill="none" stroke="#222" stroke-width="2"/>
  <line x1="600" y1="17" x2="600" y2="24" stroke="#222" stroke-width="2"/>
</svg>
<div class="abs foot-h" style="left:89px;top:3345px">About</div>
<p class="abs foot-p" style="left:89px;top:3386px;width:310px">Lorem ipsum dolor sit amet, consectetur adipiscing elit, sed do eiusmod tempor incididunt ut labore et dolore magna aliqua. Ut enim ad minim veniam, quis nostrud exercitation ullamco laboris nisi ut aliquip ex ea commodo consequat.</p>
<div class="abs foot-h" style="left:571px;top:3346px">Links</div>
<div class="abs foot-link" style="left:571px;top:3387px">Home<br>Destination Tips<br>Questions<br>Blog</div>
<div class="abs foot-link" style="left:750px;top:3387px">Gallery<br>Contact Us</div>
<div class="abs foot-h" style="left:966px;top:3346px">Contact Us</div>
<div class="abs foot-link" style="left:966px;top:3384px;font-size:13px">hello@tallfern-rides.com</div>
<div class="abs copyright">Copyright © 2020 The Company Name- All Rights Reserved.</div>
<div class="abs social-foot"><span></span><span></span><span></span><span></span><span></span></div>

</body>
</html>
```